Modern design company business card design

We are a design oriented construction firm. The owner is an architect and licensed General Contractor and accomplished furniture designer. We do new home construction and large scale remodeling and office design. We would like a design for our new business cards that is clean and modern, but relatable. We like the bright green color of our logo mixed with different shades of grey. We're also open to reinterpreting the logo.

Target Market(s)

Potential design clients,
Construction clients

Industry/Entity Type

Architecture

Contact Information for Business Card

Tall Maple Design | Build Inc. (optional with logo, Inc. optional)Jeffrey MorganOwner (optional)317.555.0148 cell317.431.8056 officejmorgan@greensquareinc.comwww.greensquareinc.com

Font styles to use
Sans Serif
Other font styles liked:
• Avenir

Requirements
Nice to have
• I like designs that have some continuity between the front and back, i.e. similar layouts or graphic elements that wrap around the card. I tend to prefer horizontal over vertical, but that's not a have to. I also tend to prefer white or recycled paper.

```html
<!DOCTYPE html>
<html lang="en">
<head>
<meta charset="utf-8">
<title>Tall Maple Design | Build – Business Card</title>
<link href="https://fonts.googleapis.com/css2?family=Mulish:wght@400;600;800&display=swap" rel="stylesheet">
<style>
  :root {
    --page: #e9eaea;
    --white: #ffffff;
    --green: #3aa845;
    --green-light: #5cc05f;
    --green-dark: #2e8f38;
    --grey-band: #b9bcbe;
    --grey-text: #5d6166;
    --charcoal: #3a3c3f;
    --charcoal-light: #6f7276;
  }
  * { box-sizing: border-box; margin: 0; padding: 0; }
  html, body { width: 1200px; height: 913px; overflow: hidden; }
  body {
    background: var(--page);
    font-family: "Mulish", sans-serif;
    position: relative;
  }
  .card {
    position: absolute;
    top: 306px;
    width: 525px;
    height: 300px;
    border-radius: 18px;
    overflow: hidden;
    box-shadow: 0 10px 28px rgba(0,0,0,.18);
  }
  .card--front { left: 45px; background: var(--white); }
  .card--back {
    left: 630px;
    background: linear-gradient(160deg, var(--charcoal-light), var(--charcoal));
  }
  .front__band {
    position: absolute; left: 0; right: 0; top: 128px; height: 10px;
    background: var(--grey-band);
  }
  .front__field {
    position: absolute; left: 0; right: 0; top: 138px; bottom: 0;
    background: linear-gradient(180deg, var(--green-light), var(--green) 45%, var(--green-dark));
  }
  .brand-name {
    position: absolute;
    color: var(--white);
    font-weight: 600;
    text-transform: uppercase;
    line-height: 1.1;
  }
  .brand-name span { display: block; }
  .brand-name .brand-sub { font-size: .6em; letter-spacing: 2px; margin-top: 5px; }
  .card--front .brand-name { left: 48px; top: 160px; font-size: 20px; letter-spacing: 1px; }
  .card--back .brand-name {
    left: 0; right: 0; top: 118px; text-align: center;
    font-size: 30px; letter-spacing: 2px;
  }
  .person {
    position: absolute; left: 190px; top: 70px;
  }
  .person__name {
    color: var(--grey-text); font-weight: 800; font-size: 19px; letter-spacing: .5px;
    text-transform: uppercase;
  }
  .person__role {
    color: var(--green); font-weight: 600; font-size: 12px; letter-spacing: 1px;
    text-transform: uppercase; margin-top: 2px;
  }
  .contact {
    position: absolute; left: 200px; top: 158px; list-style: none;
    color: var(--white); font-size: 13px; line-height: 21px;
  }
  .contact li { display: flex; align-items: center; gap: 10px; }
  .contact svg { width: 11px; height: 11px; fill: none; stroke: var(--white); stroke-width: 1.6; opacity: .85; }
</style>
</head>
<body>
  <section class="card card--front" aria-label="Business card front">
    <div class="front__field"></div>
    <div class="front__band"></div>
    <div class="brand-name"><span>Tall Maple</span><span class="brand-sub">Design | Build</span></div>
    <div class="person">
      <p class="person__name">Dennis Holloway</p>
      <p class="person__role">Owner</p>
    </div>
    <ul class="contact">
      <li><svg viewBox="0 0 12 12"><rect x="3" y="1" width="6" height="10" rx="1"/></svg>317.555.0172</li>
      <li><svg viewBox="0 0 12 12"><path d="M2 1h3l1 3-2 1a7 7 0 0 0 3 3l1-2 3 1v3a1 1 0 0 1-1 1A10 10 0 0 1 1 2a1 1 0 0 1 1-1z"/></svg>317.555.0148</li>
      <li><svg viewBox="0 0 12 12"><circle cx="6" cy="6" r="5"/><path d="M1 6h10M6 1c-3 3-3 7 0 10M6 1c3 3 3 7 0 10"/></svg>www.tallmapleinc.example</li>
      <li><svg viewBox="0 0 12 12"><rect x="1" y="2.5" width="10" height="7"/><path d="M1 2.5l5 4 5-4"/></svg>office.dholloway@tallmapleinc.example</li>
    </ul>
  </section>

  <section class="card card--back" aria-label="Business card back">
    <div class="brand-name"><span>Tall Maple</span><span class="brand-sub">Design | Build</span></div>
  </section>
</body>
</html>
```